Women's Jewellery startup needs a captivating, beautifully designed and intuitive online store

[12/24 update]

Added 2 additional documents:

Feedback on designs received so far: designer feedback.docx
Product images from catalogue: products images.docx

Please read the feedback provided on designs provided so far to guide you further on your submission. The product images can be used to create promotional banners for the site.

@@@Added a document (VELISTO JEWELLERY_checklist.docx) which can be used by designers as a checklist when submitting their designs to ensure all aspects of the requirements have been covered @@@

+++IMPORTANT BUT NOT SPECIFIED IN THE REQUIREMENTS DOCUMENT - DESIGN SHOULD INCLUDE SUPPORT FOR MOBILE FRIENDLY SITE TOO+++

***Previous experience designing Jewellery online stores preferred (not essential)***

The name of the online Jewellery store is "Velisto Jewellery" and the business is based in Hong Kong. It will be run by 2 stay at home mothers. We need a Shopify themed store designed that will achieve the following objectives in order of priority:

• Conversion: The primary objective of the design/content is to prompt the customer to make a purchase. While this may sound obvious, it is mentioned so as not to distract the design process by focusing on other objectives (which are also important). The site also needs to be optimized so as to rank high in search engine searches for relevant keywords (SEO)
• Navigation: An intuitive interface which takes away a lot of the thinking from the customer by making it obvious what they need to do when they visit the store
• Engagement: Encourages the customer to spend time on the website and share content with their social network

Where applicable, the design of the store should reflect as closely as possible the mission statements and words outlined below:

• Jewellery you’ll fall in love with
• We want every client to leave the store with a smile
• We want to be able to provide the best service we can in every situation no matter what
• We aim to increase our business by word of mouth; therefore we tell people things about our store that makes it interesting for them to share
• We love every customer, no matter how difficult things get
• We, as a team, are so well informed about our products and brands that we always have the best information for our customers
• We celebrate women here!
• We celebrate life in here!
• We celebrate beauty here!
• We celebrate families here, as jewellery often stays within families.
• We will always try to make an extra step
• We will always try to exceed the expectation of our customers
• We will go as far as we possibly can to attract a customer back to our store and connect with us
• Every client that leaves our store knows more about jewellery because we passionately told him about it
• Romantic, classic, love, warm, cool, stylish

A draft functional specification is attached with this brief. We would like the design to reflect as closely as possible the functional requirements outlined in the document. Open to suggestions to improve upon the functional requirements.

Target Market(s)

Women aged 18-55

Industry/Entity Type

Jewelry Store

Coding

Coded - Design and coding required

Number of Pages Required

5+ page

Font styles to use
Other font styles liked:
• Myriad Pro as per Logo but open to any font that complements this one

Requirements
Must have
• 1. A look that encourages the user to make a purchase
• 2. An intuitive, easy to navigate and engaging interface
• 3. Primary colour scheme as defined in the functional specification attached
• 4. Simplistic look, not too cluttered
Nice to have
• 1. Closely matching the functional requirements of the site as outlined in the requirements specification but open to any better ideas

```html
<!DOCTYPE html>
<html lang="en">
<head>
<meta charset="utf-8">
<title>Velisto Jewellery</title>
<link href="https://fonts.googleapis.com/css2?family=Open+Sans:wght@400;600&family=Lora&family=Montserrat:wght@500;600&display=swap" rel="stylesheet">
<style>
:root{
  --navy:#1b2340;
  --gold:#c9974a;
  --dark:#0f0c0c;
  --ink:#2b2b2b;
  --muted:#555;
  --line:#e2e2e2;
  --sale:#d9312b;
  --btn:#444;
  --white:#fff;
}
*{margin:0;padding:0;box-sizing:border-box}
html,body{width:1200px;height:2206px;overflow:hidden}
body{position:relative;font-family:"Open Sans",sans-serif;color:var(--ink);background:var(--white)}
.abs{position:absolute}
.topbar{left:0;top:0;width:1200px;height:38px;background:var(--navy);color:var(--white);font-size:12px}
.topbar ul{list-style:none;display:flex;gap:26px;position:absolute;right:62px;top:11px}
.topbar svg{vertical-align:-2px;margin-right:4px}
.brand{left:87px;top:0;width:160px;height:109px;background:var(--white);text-align:center;z-index:2}
.brand-mark{width:22px;height:22px;border:2px solid var(--gold);margin:22px auto 8px}
.brand-name{font-family:"Lora",serif;color:var(--gold);font-size:16px;letter-spacing:4px}
.brand-tag{font-size:8px;color:var(--gold);font-style:italic;margin-top:3px}
.mainnav{top:38px;left:0;width:1200px;height:71px;background:var(--white)}
.mainnav ul{list-style:none;display:flex;position:absolute;right:62px;top:32px;gap:0;font-size:15px;color:#333}
.mainnav li{margin-left:62px}
.hero{top:109px;left:0;width:1200px;height:450px;background:linear-gradient(90deg,#0e0a0a 0%,#1c1616 38%,#2a1c17 55%,#5a3f34 80%,#8a6a58 100%)}
.hero-photo{right:0;top:0;width:744px;height:450px;background:radial-gradient(ellipse at 62% 45%,#c89a80 0%,#7a4d38 35%,rgba(40,26,22,.2) 70%,transparent 100%)}
.hero-kicker{left:218px;top:190px;font-family:"Lora",serif;font-size:38px;color:var(--white);letter-spacing:2px}
.hero-title{left:82px;top:240px;font-family:"Montserrat",sans-serif;font-weight:600;font-size:63px;color:var(--white);letter-spacing:5px}
.hero-btn{left:243px;top:329px;width:195px;height:62px;border:1px solid var(--white);color:var(--white);font-family:"Montserrat",sans-serif;font-size:19px;letter-spacing:2px;display:flex;align-items:center;justify-content:center}
.hero-arrows{left:320px;top:412px;display:flex;gap:16px}
.promo{top:499px;width:328px;height:248px;color:var(--white);text-align:center}
.promo .kicker{margin-top:62px;font-size:16px;letter-spacing:1px}
.promo .off{font-family:"Montserrat",sans-serif;font-weight:500;font-size:56px;line-height:62px;letter-spacing:2px;border-bottom:2px solid var(--white);display:inline-block;padding:0 4px}
.promo .note{font-size:16px;margin-top:8px}
.promo.diamond{left:87px;background:radial-gradient(circle at 50% 55%,#d8d8d8,#8e8e8e 60%,#6c6c6c)}
.promo.gold{left:437px;background:radial-gradient(circle at 50% 55%,#e0c27a,#a88a55 55%,#8a8070)}
.promo.silver{left:787px;background:radial-gradient(circle at 50% 65%,#4a78b8,#1f4f8e 55%,#173a70)}
.filter{left:87px;width:223px;border:1px solid var(--line)}
.filter h3{background:var(--gold);color:var(--white);font-weight:400;font-size:12px;height:38px;line-height:44px;padding-left:17px}
.filter ul{list-style:none;padding:5px 0 4px}
.filter li{font-size:12px;height:31px;line-height:28px;padding-left:17px;position:relative}
.filter li::after{content:"";position:absolute;right:32px;top:11px;border:4px solid transparent;border-top:5px solid #888}
.filter.closed{border:none}
.filter.closed h3{height:37px;line-height:40px;position:relative}
.filter.closed h3::after{content:"";position:absolute;right:45px;top:15px;border:5px solid transparent;border-left:6px solid var(--white);border-right:none}
.catalog-title{left:338px;top:775px;font-size:22px;color:#222}
.sorts{right:85px;top:786px;display:flex;gap:36px;font-size:11px;font-weight:600}
.sorts span::after{content:"";display:inline-block;width:5px;height:5px;border-right:1px solid #333;border-bottom:1px solid #333;transform:rotate(45deg);margin:0 0 3px 5px}
.rule{left:338px;top:817px;width:777px;height:2px;background:var(--line)}
.grid{left:338px;width:777px;height:355px;border:1px solid var(--line);display:flex;gap:7px;padding:4px}
.card{width:187px;height:345px;background:#fafafa;text-align:center}
.card .shot{height:168px;background:radial-gradient(circle,#fdfdfd 0%,#e9eae8 75%)}
.card .shot.gold{background:radial-gradient(circle,#f3d88a 0%,#eceae5 45%)}
.card .shot.sapph{background:radial-gradient(circle,#5a6ab8 0%,#e4e5e6 40%)}
.card .shot.rose{background:radial-gradient(circle,#eec3a6 0%,#eeefed 35%)}
.card .shot.pink{background:radial-gradient(circle,#e27fa3 0%,#ececec 40%)}
.card h4{font-weight:600;font-size:15px;color:#334;margin-top:21px}
.price{font-size:15px;margin-top:2px}
.price s{color:var(--sale);font-size:12px;margin-left:5px}
.card p{font-size:10.5px;line-height:19px;color:#444;padding:0 12px;margin-top:8px}
.actions{display:flex;justify-content:center;gap:10px;margin-top:9px}
.qv{width:106px;height:29px;background:var(--btn);color:var(--white);font-size:12px;line-height:29px}
.fav{width:40px;height:29px;background:var(--btn);display:flex;align-items:center;justify-content:center}
.more{left:646px;top:1603px;width:161px;height:51px;background:var(--gold);color:var(--white);font-size:12px;letter-spacing:2px;display:flex;align-items:center;justify-content:center}
.footer{left:0;top:1757px;width:1200px;height:449px;background:#000;color:var(--white)}
.foot-brand{left:85px;top:110px;display:flex;align-items:center;gap:16px}
.foot-brand .sq{width:40px;height:40px;border:3px solid var(--white)}
.foot-brand span{font-family:"Lora",serif;font-size:30px;letter-spacing:8px}
.fcol h5{font-family:"Montserrat",sans-serif;font-weight:500;font-size:17px;letter-spacing:1px;padding-bottom:14px;border-bottom:1px solid #333;width:157px}
.fcol ul{list-style:none;margin-top:14px;font-size:11px;line-height:25px}
.social{left:85px;top:316px;display:flex;gap:22px}
.social i{width:22px;height:22px;border-radius:50%;background:var(--white)}
.newsletter-input{left:631px;top:297px;width:306px;height:50px;background:var(--white);color:#aaa;font-style:italic;font-size:11px;padding:19px 26px}
.newsletter-btn{left:947px;top:297px;width:168px;height:50px;background:#ccc;color:#222;font-weight:600;font-size:16px;display:flex;align-items:center;justify-content:center}
.foot-rule{left:85px;top:380px;width:1030px;height:1px;background:#333}
.copy{left:85px;top:407px;font-size:12px}
.cards{right:85px;top:403px;display:flex;gap:7px}
.cards i{width:35px;height:24px;border-radius:3px;background:#e8e8e8}
</style>
</head>
<body>
<header class="abs topbar">
  <ul>
    <li><svg width="10" height="11" viewBox="0 0 10 11"><circle cx="5" cy="3" r="3" fill="#fff"/><path d="M0 11c0-4 10-4 10 0z" fill="#fff"/></svg>Sign in</li>
    <li><svg width="12" height="11" viewBox="0 0 12 11"><path d="M6 11L1 6a3 3 0 015-4 3 3 0 015 4z" fill="#fff"/></svg>Wishlist</li>
    <li><svg width="13" height="11" viewBox="0 0 13 11"><path d="M0 1h2l2 6h7l2-5H4" fill="none" stroke="#fff" stroke-width="1.5"/><circle cx="5" cy="10" r="1" fill="#fff"/><circle cx="10" cy="10" r="1" fill="#fff"/></svg>My Cart (0)</li>
    <li>GBP ▾</li>
    <li><svg width="12" height="12" viewBox="0 0 12 12"><circle cx="5" cy="5" r="3.7" fill="none" stroke="#fff" stroke-width="2"/><path d="M8 8l3 3" stroke="#fff" stroke-width="2"/></svg></li>
  </ul>
</header>
<div class="abs brand">
  <div class="brand-mark"></div>
  <div class="brand-name">VELISTO</div>
  <div class="brand-tag">Jewellery you'll fall in love with</div>
</div>
<nav class="abs mainnav">
  <ul><li>Home</li><li>Products</li><li>Our Story</li><li>FAQ</li><li>Blog</li><li>Contact Us</li></ul>
</nav>

<section class="abs hero">
  <div class="abs hero-photo" role="img" aria-label="Portrait of a woman wearing a diamond and ruby necklace"></div>
  <div class="abs hero-kicker">We celebrate</div>
  <h1 class="abs hero-title">BEAUTY HERE!</h1>
  <div class="abs hero-btn">Shop Now &gt;</div>
  <div class="abs hero-arrows">
    <svg width="8" height="12" viewBox="0 0 8 12"><path d="M6 1L1 6l5 5" fill="none" stroke="#fff" stroke-width="2"/></svg>
    <svg width="8" height="12" viewBox="0 0 8 12"><path d="M2 1l5 5-5 5" fill="none" stroke="#fff" stroke-width="2"/></svg>
  </div>
</section>

<div class="abs promo diamond" role="img" aria-label="Diamond rings offer">
  <div class="kicker">EXTRA</div><div class="off">10% OFF</div><div class="note">Diamond rings till March 31st, 2018</div>
</div>
<div class="abs promo gold" role="img" aria-label="Gold rings offer">
  <div class="kicker">EXTRA</div><div class="off">20% OFF</div><div class="note">Gold rings till March 31st, 2018</div>
</div>
<div class="abs promo silver" role="img" aria-label="Silver rings offer">
  <div class="kicker">EXTRA</div><div class="off">30% OFF</div><div class="note">Silver rings till March 31st, 2018</div>
</div>

<aside>
  <div class="abs filter" style="top:771px"><h3>Type</h3><ul><li>Rings</li><li>Necklaces</li><li>Bracelets</li><li>Earring</li><li>Charms</li></ul></div>
  <div class="abs filter" style="top:979px"><h3>Collection</h3><ul><li>Lorem Ipsum</li><li>Lorem</li><li>Lorem Ipsum</li><li>Ipsum</li><li>Lorem Ipsum</li></ul></div>
  <div class="abs filter" style="top:1188px"><h3>Metal</h3><ul><li>R10K Rose Gold</li><li>14K Gold Rose</li><li>18K Gold Rose</li><li>10K Yellow Gold</li><li>14K Yellow Rose</li><li>18K Yellow Rose</li><li>Silver, Gold plated</li><li>Silver plated</li></ul></div>
  <div class="abs filter closed" style="top:1488px"><h3>Gemstone</h3></div>
  <div class="abs filter closed" style="top:1534px"><h3>Price range</h3></div>
</aside>

<h2 class="abs catalog-title" style="font-weight:400">Product</h2>
<div class="abs sorts"><span>Our Favourites</span><span>What's new</span><span>Price</span></div>
<div class="abs rule"></div>

<div class="abs grid" style="top:832px">
  <article class="card"><div class="shot" role="img" aria-label="Silver diamond solitaire ring"></div><h4>Lorem Ipsum</h4><div class="price">$ 99.90<s>$ 125.00</s></div><p>Lorem Ipsum is simply dummy text of the printing and typesetting industry.</p><div class="actions"><span class="qv">Quick View</span><span class="fav"><svg width="13" height="11" viewBox="0 0 12 11"><path d="M6 11L1 6a3 3 0 015-4 3 3 0 015 4z" fill="#fff"/></svg></span></div></article>
  <article class="card"><div class="shot sapph" role="img" aria-label="Sapphire halo ring"></div><h4>Lorem Ipsum</h4><div class="price">$ 99.90<s>$ 125.00</s></div><p>Lorem Ipsum is simply dummy text of the printing and typesetting industry.</p><div class="actions"><span class="qv">Quick View</span><span class="fav"><svg width="13" height="11" viewBox="0 0 12 11"><path d="M6 11L1 6a3 3 0 015-4 3 3 0 015 4z" fill="#fff"/></svg></span></div></article>
  <article class="card"><div class="shot gold" role="img" aria-label="Pair of gold bands"></div><h4>Lorem Ipsum</h4><div class="price">$ 99.90<s>$ 125.00</s></div><p>Lorem Ipsum is simply dummy text of the printing and typesetting industry.</p><div class="actions"><span class="qv">Quick View</span><span class="fav"><svg width="13" height="11" viewBox="0 0 12 11"><path d="M6 11L1 6a3 3 0 015-4 3 3 0 015 4z" fill="#fff"/></svg></span></div></article>
  <article class="card"><div class="shot rose" role="img" aria-label="Rose gold diamond ring"></div><h4>Lorem Ipsum</h4><div class="price">$ 99.90<s>$ 125.00</s></div><p>Lorem Ipsum is simply dummy text of the printing and typesetting industry.</p><div class="actions"><span class="qv">Quick View</span><span class="fav"><svg width="13" height="11" viewBox="0 0 12 11"><path d="M6 11L1 6a3 3 0 015-4 3 3 0 015 4z" fill="#fff"/></svg></span></div></article>
</div>
<div class="abs grid" style="top:1215px">
  <article class="card"><div class="shot gold" role="img" aria-label="Gold flower stud earrings"></div><h4>Lorem Ipsum</h4><div class="price">$ 99.90<s>$ 125.00</s></div><p>Lorem Ipsum is simply dummy text of the printing and typesetting industry.</p><div class="actions"><span class="qv">Quick View</span><span class="fav"><svg width="13" height="11" viewBox="0 0 12 11"><path d="M6 11L1 6a3 3 0 015-4 3 3 0 015 4z" fill="#fff"/></svg></span></div></article>
  <article class="card"><div class="shot gold" role="img" aria-label="Stack of gold bangles"></div><h4>Lorem Ipsum</h4><div class="price">$ 99.90<s>$ 125.00</s></div><p>Lorem Ipsum is simply dummy text of the printing and typesetting industry.</p><div class="actions"><span class="qv">Quick View</span><span class="fav"><svg width="13" height="11" viewBox="0 0 12 11"><path d="M6 11L1 6a3 3 0 015-4 3 3 0 015 4z" fill="#fff"/></svg></span></div></article>
  <article class="card"><div class="shot pink" role="img" aria-label="Silver ring with pink stone"></div><h4>Lorem Ipsum</h4><div class="price">$ 99.90<s>$ 125.00</s></div><p>Lorem Ipsum is simply dummy text of the printing and typesetting industry.</p><div class="actions"><span class="qv">Quick View</span><span class="fav"><svg width="13" height="11" viewBox="0 0 12 11"><path d="M6 11L1 6a3 3 0 015-4 3 3 0 015 4z" fill="#fff"/></svg></span></div></article>
  <article class="card"><div class="shot gold" role="img" aria-label="Gold drop earrings"></div><h4>Lorem Ipsum</h4><div class="price">$ 99.90<s>$ 125.00</s></div><p>Lorem Ipsum is simply dummy text of the printing and typesetting industry.</p><div class="actions"><span class="qv">Quick View</span><span class="fav"><svg width="13" height="11" viewBox="0 0 12 11"><path d="M6 11L1 6a3 3 0 015-4 3 3 0 015 4z" fill="#fff"/></svg></span></div></article>
</div>
<div class="abs more">View More &gt;&gt;</div>

<footer class="abs footer">
  <div class="abs foot-brand"><div class="sq"></div><span>VELISTO</span></div>
  <div class="abs fcol" style="left:487px;top:61px"><h5>ABOUT US</h5><ul><li>Our Story</li><li>Wholesale inquiries</li></ul></div>
  <div class="abs fcol" style="left:721px;top:61px"><h5>SHOPPING</h5><ul><li>Orders</li><li>Wishlist</li><li>Size Guide</li></ul></div>
  <div class="abs fcol" style="left:953px;top:61px"><h5>CUSTOMER CARE</h5><ul><li>Returns</li><li>FAQs</li><li>Care &amp; Warranty</li><li>Contact Us</li></ul></div>
  <div class="abs fcol" style="left:90px;top:254px"><h5 style="width:157px">FOLLOW US</h5></div>
  <div class="abs social"><i aria-label="Social link"></i><i aria-label="Social link"></i><i aria-label="Social link"></i></div>
  <div class="abs fcol" style="left:629px;top:254px"><h5 style="border:none">NEWSLETTER SIGN UP</h5></div>
  <div class="abs newsletter-input">Your Email</div>
  <div class="abs newsletter-btn">SUBMIT</div>
  <div class="abs foot-rule"></div>
  <div class="abs copy">Copyright © 2017. Velisto Jewellery. All rights reserved.</div>
  <div class="abs cards" aria-label="Accepted payment methods"><i></i><i></i><i></i><i></i><i></i></div>
</footer>
</body>
</html>
```